VENTURE CAPITAL GROUP BUSINESS CARD DESIGN

Venture Capital Group based in SF looking for a bold business card design. No trendy colour explosion, 3D effects etc. Just "simple" optical effects. Works on your brain, keeps your eye focused and sticks to your mind.
Target Market(s)
Technology startups
Industry/Entity Type
Venture Capital
Contact Information for Business Card
DESMOND WHITLAKE
MANAGING PARTNER
187 FENWORTH ST SAN FRANCISCO, CA 94187
415.555.0142 O
415.555.0147 F
415.555.0193 C
desmond@veldtmoorcapital.ventures

```html
<!DOCTYPE html>
<html lang="en">
<head>
<meta charset="utf-8">
<title>Veldtmoor Capital Group – Business Card</title>
<link href="https://fonts.googleapis.com/css2?family=Lora:wght@500;600&family=Source+Sans+3:wght@400&display=swap" rel="stylesheet">
<style>
  :root {
    --stage: #a8a5a5;
    --card-dark: #141516;
    --card-light: #f7f7f6;
    --brand-green: #2f8f3a;
    --green-light: #4fb04f;
    --green-deep: #1f7a2c;
    --ink: #555657;
    --ink-soft: #6a6b6c;
    --rule: #dedede;
    --band-grey: #9a9a9a;
    --disc-dark: #262728;
    --disc-light: #e4e4e4;
    --white: #ffffff;
  }
  * { margin: 0; padding: 0; box-sizing: border-box; }
  html, body { width: 1200px; height: 1200px; overflow: hidden; }
  body { background: var(--stage); position: relative; font-family: "Source Sans 3", sans-serif; }

  .card { position: absolute; overflow: hidden; }
  .card--front { left: 237px; top: 116px; width: 715px; height: 422px; background: var(--card-dark); }
  .card--back  { left: 230px; top: 644px; width: 714px; height: 417px; background: var(--card-light); }

  .brand-disc { position: absolute; border-radius: 50%; }
  .card--front .brand-disc { left: 275px; top: 90px; width: 165px; height: 165px; background: var(--disc-dark); }
  .card--back .brand-disc { left: 104px; top: 96px; width: 120px; height: 120px; background: var(--disc-light); }

  .brand-name {
    position: absolute; font-family: "Lora", serif; font-weight: 500;
    color: var(--brand-green); text-align: center; line-height: 1;
  }
  .brand-name span { display: block; }
  .card--front .brand-name { left: 0; width: 100%; top: 278px; }
  .card--front .brand-name .brand-main { font-size: 46px; letter-spacing: 2px; }
  .card--front .brand-name .brand-sub { font-size: 14px; letter-spacing: 8px; margin-top: 6px; }
  .card--back .brand-name { left: 20px; width: 288px; top: 244px; }
  .card--back .brand-name .brand-main { font-size: 31px; letter-spacing: 1px; }
  .card--back .brand-name .brand-sub { font-size: 10px; letter-spacing: 5px; margin-top: 4px; }

  .divider { position: absolute; left: 327px; top: 59px; width: 1px; height: 271px; background: var(--rule); }

  .person { position: absolute; left: 360px; top: 95px; }
  .person__name { font-family: "Lora", serif; font-weight: 600; font-size: 26px; color: var(--ink); line-height: 1.1; }
  .person__title { font-family: "Lora", serif; font-weight: 500; font-size: 17px; color: var(--ink-soft); margin-top: 2px; }

  .contact { position: absolute; left: 360px; top: 176px; list-style: none; }
  .contact li { display: flex; align-items: center; height: 23.3px; font-size: 17.5px; color: var(--ink); }
  .contact svg { width: 18px; height: 16px; margin-right: 17px; fill: var(--brand-green); flex: none; }

  .address { position: absolute; left: 360px; top: 277px; font-size: 17.5px; color: var(--ink); }

  .band-grey { position: absolute; left: 0; top: 392px; width: 320px; height: 25px; background: var(--band-grey); }
  .band-green {
    position: absolute; left: 294px; top: 365px; width: 420px; height: 52px;
    background: linear-gradient(90deg, var(--green-deep), var(--green-light));
    clip-path: polygon(41px 0, 100% 0, 100% 100%, 0 100%);
  }
  .website { position: absolute; left: 360px; top: 375px; font-size: 17.5px; color: var(--white); }
</style>
</head>
<body>

<section class="card card--front" aria-label="Card front">
  <div class="brand-disc"></div>
  <div class="brand-name">
    <span class="brand-main">VELDTMOOR</span>
    <span class="brand-sub">CAPITAL GROUP</span>
  </div>
</section>

<section class="card card--back" aria-label="Card back">
  <div class="brand-disc"></div>
  <div class="brand-name">
    <span class="brand-main">VELDTMOOR</span>
    <span class="brand-sub">CAPITAL GROUP</span>
  </div>

  <div class="divider"></div>

  <div class="person">
    <p class="person__name">Desmond Whitlake</p>
    <p class="person__title">Managing Partner</p>
  </div>

  <ul class="contact">
    <li>
      <svg viewBox="0 0 18 16" aria-hidden="true"><path d="M1 5c0-2 4-3.5 8-3.5S17 3 17 5v1.5h-4V5H5v1.5H1z M4 8h10l2 7H2z"/></svg>
      415.555.0142
    </li>
    <li>
      <svg viewBox="0 0 18 16" aria-hidden="true"><path d="M5 1h8v4H5z M1 6h16v6h-3v-3H4v3H1z M5 10h8v5H5z"/></svg>
      415.555.0147
    </li>
    <li>
      <svg viewBox="0 0 18 16" aria-hidden="true"><path d="M5 0h8a1 1 0 0 1 1 1v14a1 1 0 0 1-1 1H5a1 1 0 0 1-1-1V1a1 1 0 0 1 1-1z M6 2v10h6V2z"/></svg>
      415.555.0193
    </li>
    <li>
      <svg viewBox="0 0 18 16" aria-hidden="true"><path d="M1 3h16v10H1z M2.5 4.5v0.6L9 9.5l6.5-4.4v-0.6z" fill-rule="evenodd"/></svg>
      desmond@veldtmoorcapital.ventures
    </li>
  </ul>

  <p class="address">187 Fenworth St San Francisco, CA 94187</p>

  <div class="band-grey"></div>
  <div class="band-green"></div>
  <p class="website">www.veldtmoorcapital.ventures</p>
</section>

</body>
</html>
```